Beauty Salon Mentor Illustration

Hi There, I'm Belinda and I'm a Beauty Salon owner mentor. We are needing 5 different illustration design for a beauty salon coaching business. The pictures will be used on our website next to a small description about our course out line.
Course and what the illustrations will be referring to below:
1. Launch Pad Parlour -Make your dream of owning a salon a reality.
Three options of start-up training and support, teaching must-know insights for beauty therapists who are ready to take the leap to salon owner and want to do it right. Whether you’ve been in the beauty industry a short time or forever, Launch Pad Parlour will set you up for salon success.

2. Chairs Filled Fast - Attract more clients with simple, strategic digital marketing. Chairs Filled Fast educates on the ins and outs of sponsored social media ads. With easy-to-follow video training, you’ll establish your online presence and increase salon bookings.
Learn how to show up on social media with effective strategies that work. Choose our Handled Entirely system, or learn to do it all with our DIY system.

3. Momentum Studio Plan - Transform your salon and your life. Our most tailored program, Momentum Studio Plan offers coaching memberships with Bloom Beauty Hub’s Founder- Belinda. With our results focused framework, you will upskill employees, improve the working environment of the salon and receive leading beauty industry training as we dive into the culture and mindset of your salon. With Belinda as your business mentor and biggest cheerleader get ready to achieve your business goals and move forward with rapid growth.

4. Revive Parlour Path - Successfully put your salon back on the map.
Step into today’s beauty landscape with optimised marketing and industry expertise. If your salon’s been open for a year or even twenty years, Revive Parlour Path will elevate your business, renew your love for your salon and set you up to generate more income. Stand out from the competition as you increase online presence, learn key business development processes and see real results.

5. Skillset Studio Plan - Successfully Upskill and Level Up Your Salon. Skillset Studio Plan offers three training options- In Salon, Online & Diploma of Beauty Therapy. Whether you have your own salon or want to become qualified, Bloom Beauty Hub’s- Skillset Studio Plan adds industry authority and brings specialist expertise to all level of beauty therapists.
Our coaching is based in Australia, aim at female beauty salon owners who are ready to take their business to the next level.

In the files below is just a picture of me so you know who i am. We are wanting the illusion to appeal to a wide audience.

I am the business and everyone i attract into our coaching program works closely with me.

Target Market(s)

Beauty Salon owners; women

Font styles to use
Sans Serif

Colors
fce8d3
fee3d4
fff5ef
fff3d1
f9bb94
fcca95

Requirements
Must have
• Must be relatable to the brief, designs must look great together on the website or separately on their own.
Nice to have
• Industry relatable, engaging to the eye.
Should not have
• i would prefer if there wasn't any words on the illusion

```html
<!DOCTYPE html>
<html lang="en">
<head>
<meta charset="utf-8">
<title>Beauty Salon Mentor Illustration</title>
<link href="https://fonts.googleapis.com/css2?family=Archivo+Black&family=Montserrat:wght@500&family=Open+Sans:wght@300;400&display=swap" rel="stylesheet">
<style>
:root{
  --board:#f6e4dc;
  --ink:#2e2e2e;
  --body:#4a4a4a;
  --pink:#f07891;
  --title-pink:#f2728c;
  --peach:#f9bb94;
  --orange:#f5975a;
  --blush:#fee3d4;
  --blush-line:#f0aa98;
  --cream:#fff5ef;
  --cream-line:#f1bcae;
  --butter:#fff3d1;
  --slate:#3d5675;
  --pale-gold:#fde9b8;
  --blue:#2f72d3;
  --sky:#6fb6e8;
  --sky-light:#cfe9fb;
  --white:#ffffff;
}
*{box-sizing:border-box;margin:0;padding:0}
html,body{width:1200px;height:1032px;overflow:hidden;background:var(--board)}
body{position:relative;font-family:"Open Sans",sans-serif;color:var(--ink)}

.board-logo{position:absolute;left:17px;top:36px;font:400 13px "Open Sans",sans-serif;color:#555;letter-spacing:.5px}
.board-title{position:absolute;left:18px;top:100px;font:500 68px/78px "Montserrat",sans-serif;letter-spacing:1px;color:#333}
.board-title .accent{color:var(--title-pink)}

.card{position:absolute;overflow:hidden;box-shadow:0 2px 5px rgba(120,80,60,.18)}
.card > *{position:absolute}
.brand{font:400 6.5px "Open Sans",sans-serif;color:#555;white-space:nowrap}
.handle{font:300 7px "Open Sans",sans-serif;white-space:nowrap}
.headline{font-family:"Archivo Black",sans-serif;line-height:1.08;color:var(--ink)}
.subhead{font-family:"Open Sans",sans-serif;font-weight:300;line-height:1.15}
.copy{font-size:6.6px;line-height:1.38;text-align:justify;color:var(--body)}
.copy p + p{margin-top:0}
.contact{display:flex;justify-content:space-between;font-size:4.6px;white-space:nowrap}
.contact span{display:flex;align-items:center;gap:2px}
.contact svg{width:5px;height:5px}
.art{display:block}

/* momentum */
.momentum{background:var(--white)}
.momentum .handle,.momentum .subhead,.momentum .contact{color:var(--blue)}
.momentum .swoosh{top:0;right:0}

/* launch pad */
.launch{background:var(--blush)}
.launch .frame{inset:9px;border:1px solid var(--blush-line);border-radius:5px}
.launch .handle,.launch .subhead,.launch .contact{color:var(--pink)}

/* revive */
.revive{background:#fdf0e9}
.revive .frame{inset:9px;border:1px solid var(--cream-line);border-radius:5px;background:var(--cream)}
.revive .handle,.revive .subhead,.revive .contact{color:var(--pink)}

/* chairs */
.chairs{background:var(--white)}
.chairs .handle,.chairs .subhead,.chairs .contact{color:var(--orange)}
.chairs .headline .mark{border-bottom:2px solid var(--ink)}

/* skillset */
.skillset{background:var(--butter)}
.skillset .panel{inset:10px 9px 11px 9px;background:var(--slate);border-radius:5px}
.skillset .headline{color:var(--white)}
.skillset .subhead{color:var(--pale-gold)}
.skillset .brand{color:var(--pale-gold);display:flex;align-items:center;gap:2px}
.skillset .brand i{display:block;width:5px;height:5px;background:var(--pale-gold)}
.skillset .handle,.skillset .copy,.skillset .contact{color:var(--white)}
</style>
</head>
<body>

<svg width="0" height="0" style="position:absolute" aria-hidden="true">
  <symbol id="i-phone" viewBox="0 0 10 10"><path d="M2 1l2 2-1 1.3c.6 1.2 1.5 2.1 2.7 2.7L7 6l2 2-1.3 1.3C4.5 9 1 5.5.7 2.3z" fill="currentColor"/></symbol>
  <symbol id="i-mail" viewBox="0 0 10 10"><rect x=".8" y="2" width="8.4" height="6" fill="none" stroke="currentColor"/><path d="M.8 2l4.2 3.4L9.2 2" fill="none" stroke="currentColor"/></symbol>
  <symbol id="i-globe" viewBox="0 0 10 10"><circle cx="5" cy="5" r="4.2" fill="none" stroke="currentColor"/><ellipse cx="5" cy="5" rx="1.8" ry="4.2" fill="none" stroke="currentColor"/><path d="M.8 5h8.4" stroke="currentColor"/></symbol>
</svg>

<div class="board-logo">Bloom Beauty Hub</div>
<h1 class="board-title">BEAUTY SALON<br>MENTOR<br><span class="accent">ILLUSTRATION</span></h1>

<!-- Momentum Studio Plan, compact -->
<section class="card momentum" style="left:600px;top:25px;width:237px;height:316px">
  <svg class="swoosh" width="150" height="200" viewBox="0 0 150 200"><path d="M40 0H150V200C125 170 132 110 110 70 95 40 70 15 40 0Z" fill="var(--sky-light)"/><path d="M80 0H150V180C138 150 140 100 125 65 115 40 100 15 80 0Z" fill="var(--sky)"/></svg>
  <div class="art" role="img" aria-label="Circular illustration of a woman receiving a facial surrounded by skincare items" style="left:108px;top:48px;width:110px;height:110px;border-radius:50%;background:radial-gradient(circle,#eef6fd 55%,#dbeefa);border:3px solid #fff;box-shadow:0 0 0 1px #bcdcf4"></div>
  <div class="brand" style="left:11px;top:14px">Bloom Beauty Hub</div>
  <div class="handle" style="right:46px;top:23px">@bloombeautyhub</div>
  <h2 class="headline" style="left:12px;top:56px;font-size:16px">Momentum<br>Studio<br>Plan</h2>
  <p class="subhead" style="left:12px;top:121px;font-size:17.5px;width:120px">Transform your salon and your life.</p>
  <div class="copy" style="left:10px;top:204px;width:217px;font-size:6.2px">Our most tailored program, Momentum Studio Plan offers coaching memberships with Bloom Beauty Hub’s Founder- Belinda. With our results focused framework, you will upskill employees, improve the working environment of the salon and receive leading beauty industry training as we dive into the culture and mindset of your salon. With Belinda as your business mentor and biggest cheerleader get ready to achieve your business goals and move forward with rapid growth.</div>
  <div class="contact" style="left:12px;right:10px;top:298px"><span><svg><use href="#i-phone"/></svg>(+614) 5550 2187</span><span><svg><use href="#i-mail"/></svg>hello@bloombeautyhub.com</span><span><svg><use href="#i-globe"/></svg>www.bloombeautyhub.com</span></div>
</section>

<!-- Momentum Studio Plan, wide -->
<section class="card momentum" style="left:847px;top:25px;width:316px;height:316px">
  <svg class="swoosh" width="170" height="200" viewBox="0 0 170 200"><path d="M50 0H170V200C140 170 150 110 128 70 110 38 82 14 50 0Z" fill="var(--sky-light)"/><path d="M95 0H170V185C156 150 160 100 142 62 130 38 115 15 95 0Z" fill="var(--sky)"/></svg>
  <div class="art" role="img" aria-label="Circular illustration of a woman receiving a facial surrounded by skincare items" style="left:176px;top:60px;width:120px;height:120px;border-radius:50%;background:radial-gradient(circle,#eef6fd 55%,#dbeefa);border:3px solid #fff;box-shadow:0 0 0 1px #bcdcf4"></div>
  <div class="brand" style="left:20px;top:32px;font-size:7.5px">Bloom Beauty Hub</div>
  <div class="handle" style="right:50px;top:34px;font-size:7.5px">@bloombeautyhub</div>
  <h2 class="headline" style="left:22px;top:62px;font-size:20px">Momentum<br>Studio Plan</h2>
  <p class="subhead" style="left:21px;top:113px;font-size:20px;width:160px">Transform your salon and your life.</p>
  <div class="copy" style="left:20px;top:197px;width:278px;font-size:7.5px">Our most tailored program, Momentum Studio Plan offers coaching memberships with Bloom Beauty Hub’s Founder- Belinda. With our results focused framework, you will upskill employees, improve the working environment of the salon and receive leading beauty industry training as we dive into the culture and mindset of your salon. With Belinda as your business mentor and biggest cheerleader get ready to achieve your business goals and move forward with rapid growth.</div>
  <div class="contact" style="left:21px;right:22px;top:291px;font-size:6.8px"><span><svg><use href="#i-phone"/></svg>(+614) 5550 2187</span><span><svg><use href="#i-mail"/></svg>hello@bloombeautyhub.com</span><span><svg><use href="#i-globe"/></svg>www.bloombeautyhub.com</span></div>
</section>

<!-- Launch Pad Parlour, compact -->
<section class="card launch" style="left:17px;top:355px;width:236px;height:315px">
  <div class="frame"></div>
  <div class="brand" style="left:18px;top:20px">Bloom Beauty Hub</div>
  <div class="handle" style="right:20px;top:26px">@bloombeautyhub</div>
  <h2 class="headline" style="left:18px;top:37px;font-size:14px">LAUNCH PAD PARLOUR</h2>
  <p class="subhead" style="left:18px;top:59px;font-size:16px;width:200px">Make your dream of owning a salon a reality.</p>
  <div class="art" role="img" aria-label="Illustration of a woman with a hair towel washing her face among leaves" style="left:70px;top:105px;width:108px;height:105px;border-radius:50% 50% 45% 45%;background:radial-gradient(circle at 50% 45%,#f7dcc4 40%,#c9c1a4 75%,#a9a88a)"></div>
  <div class="copy" style="left:18px;top:219px;width:200px;font-size:7px">Three options of start-up training and support, teaching must-know insights for beauty therapists who are ready to take the leap to salon owner and want to do it right. Whether you’ve been in the beauty industry a short time or forever, Launch Pad Parlour will set you up for salon success.</div>
  <div class="contact" style="left:24px;right:20px;top:296px"><span><svg><use href="#i-phone"/></svg>(+614) 5550 2187</span><span><svg><use href="#i-mail"/></svg>hello@bloombeautyhub.com</span><span><svg><use href="#i-globe"/></svg>www.bloombeautyhub.com</span></div>
</section>

<!-- Launch Pad Parlour, wide -->
<section class="card launch" style="left:271px;top:355px;width:314px;height:315px">
  <div class="frame"></div>
  <div class="brand" style="left:22px;top:26px;font-size:7px">Bloom Beauty Hub</div>
  <div class="handle" style="right:22px;top:34px;font-size:7.5px">@bloombeautyhub</div>
  <h2 class="headline" style="left:20px;top:47px;font-size:20px">LAUNCH PAD PARLOUR</h2>
  <p class="subhead" style="left:20px;top:75px;font-size:16.5px;width:275px">Make your dream of owning a salon a reality.</p>
  <div class="art" role="img" aria-label="Illustration of a woman with a hair towel washing her face among leaves" style="left:105px;top:122px;width:105px;height:95px;border-radius:50% 50% 45% 45%;background:radial-gradient(circle at 50% 45%,#f7dcc4 40%,#c9c1a4 75%,#a9a88a)"></div>
  <div class="copy" style="left:20px;top:229px;width:275px;font-size:7.5px">Three options of start-up training and support, teaching must-know insights for beauty therapists who are ready to take the leap to salon owner and want to do it right. Whether you’ve been in the beauty industry a short time or forever, Launch Pad Parlour will set you up for salon success.</div>
  <div class="contact" style="left:20px;right:21px;top:289px;font-size:7.4px"><span><svg><use href="#i-phone"/></svg>(+614) 5550 2187</span><span><svg><use href="#i-mail"/></svg>hello@bloombeautyhub.com</span><span><svg><use href="#i-globe"/></svg>www.bloombeautyhub.com</span></div>
</section>

<!-- Revive Parlour Path, compact -->
<section class="card revive" style="left:602px;top:355px;width:235px;height:314px">
  <div class="frame"></div>
  <div class="brand" style="left:17px;top:22px">Bloom Beauty Hub</div>
  <div class="handle" style="right:18px;top:28px">@bloombeautyhub</div>
  <h2 class="headline" style="left:17px;top:39px;font-size:15px">Revive Parlour Path</h2>
  <p class="subhead" style="left:17px;top:60px;font-size:16px;width:200px">Successfully put your salon back on the map.</p>
  <div class="art" role="img" aria-label="Illustration of a woman holding a large arrow beside a hashtag and a potted plant" style="left:75px;top:104px;width:85px;height:96px;border-radius:45% 45% 10% 10%;background:linear-gradient(180deg,#d9cfc8,#f3dac9 60%,#f29bb0)"></div>
  <div class="copy" style="left:17px;top:209px;width:200px;font-size:6.9px">Step into today’s beauty landscape with optimised marketing and industry expertise. If your salon’s been open for a year or even twenty years, Revive Parlour Path will elevate your business, renew your love for your salon and set you up to generate more income. Stand out from the competition as you increase online presence, learn key business development processes and see real</div>
  <div class="contact" style="left:24px;right:18px;top:295px"><span><svg><use href="#i-phone"/></svg>(+614) 5550 2187</span><span><svg><use href="#i-mail"/></svg>hello@bloombeautyhub.com</span><span><svg><use href="#i-globe"/></svg>www.bloombeautyhub.com</span></div>
</section>

<!-- Revive Parlour Path, wide -->
<section class="card revive" style="left:854px;top:355px;width:314px;height:314px">
  <div class="frame"></div>
  <div class="brand" style="left:22px;top:24px;font-size:7px">Bloom Beauty Hub</div>
  <div class="handle" style="right:22px;top:32px;font-size:7.5px">@bloombeautyhub</div>
  <h2 class="headline" style="left:20px;top:44px;font-size:21px">Revive Parlour Path</h2>
  <p class="subhead" style="left:22px;top:70px;font-size:16.5px;width:275px">Successfully put your salon back on the map.</p>
  <div class="art" role="img" aria-label="Illustration of a woman holding a large arrow beside a hashtag and a potted plant" style="left:119px;top:108px;width:82px;height:92px;border-radius:45% 45% 10% 10%;background:linear-gradient(180deg,#d9cfc8,#f3dac9 60%,#f29bb0)"></div>
  <div class="copy" style="left:20px;top:206px;width:275px;font-size:7.6px;line-height:1.6">Step into today’s beauty landscape with optimised marketing and industry expertise. If your salon’s been open for a year or even twenty years, Revive Parlour Path will elevate your business, renew your love for your salon and set you up to generate more income. Stand out from the competition as you increase online presence, learn key business development processes and see real results.</div>
  <div class="contact" style="left:20px;right:20px;top:289px;font-size:7.4px"><span><svg><use href="#i-phone"/></svg>(+614) 5550 2187</span><span><svg><use href="#i-mail"/></svg>hello@bloombeautyhub.com</span><span><svg><use href="#i-globe"/></svg>www.bloombeautyhub.com</span></div>
</section>

<!-- Chairs Filled Fast, compact -->
<section class="card chairs" style="left:17px;top:692px;width:235px;height:314px">
  <svg style="left:0;top:0" width="235" height="200" viewBox="0 0 235 200"><path fill-rule="evenodd" fill="var(--peach)" d="M95 20a150 150 0 1 0 300 0a150 150 0 1 0 -300 0ZM118 5a135 140 0 1 0 270 0a135 140 0 1 0 -270 0Z"/></svg>
  <div class="art" role="img" aria-label="Illustration of a woman relaxing with a phone and coffee beside a plant and a floating screen" style="left:120px;top:22px;width:108px;height:90px;border-radius:8px;background:linear-gradient(135deg,#cfc7b4,#fbe3d6 45%,#f3a3b8)"></div>
  <div class="brand" style="left:11px;top:15px">Bloom Beauty Hub</div>
  <div class="handle" style="left:11px;top:58px">@bloombeautyhub</div>
  <h2 class="headline" style="left:11px;top:92px;font-size:16.5px">Chairs<br><span class="mark">Filled Fast</span></h2>
  <p class="subhead" style="left:11px;top:140px;font-size:13.5px;width:180px">Attract more clients with simple, strategic digital marketing.</p>
  <div class="copy" style="left:11px;top:206px;width:213px;font-size:7px;line-height:1.3">Chairs Filled Fast educates on the ins and outs of sponsored social media ads. With easy-to-follow video training, you’ll establish your online presence and increase salon bookings.<br><br>Learn how to show up on social media with effective strategies that work. Choose our Handled Entirely system, or learn to do it all with our DIY system.</div>
  <div class="contact" style="left:11px;right:10px;top:298px"><span><svg><use href="#i-phone"/></svg>(+614) 5550 2187</span><span><svg><use href="#i-mail"/></svg>hello@bloombeautyhub.com</span><span><svg><use href="#i-globe"/></svg>www.bloombeautyhub.com</span></div>
</section>

<!-- Chairs Filled Fast, wide -->
<section class="card chairs" style="left:271px;top:692px;width:315px;height:314px">
  <svg style="left:0;top:0" width="315" height="240" viewBox="0 0 315 240"><path fill-rule="evenodd" fill="var(--peach)" d="M140 30a190 190 0 1 0 380 0a190 190 0 1 0 -380 0ZM165 12a175 178 0 1 0 350 0a175 178 0 1 0 -350 0Z"/></svg>
  <div class="art" role="img" aria-label="Illustration of a woman relaxing with a phone and coffee beside a plant and a floating screen" style="left:180px;top:30px;width:118px;height:88px;border-radius:8px;background:linear-gradient(135deg,#cfc7b4,#fbe3d6 45%,#f3a3b8)"></div>
  <div class="brand" style="left:19px;top:26px;font-size:7.5px">Bloom Beauty Hub</div>
  <div class="handle" style="left:19px;top:63px;font-size:7.5px">@bloombeautyhub</div>
  <h2 class="headline" style="left:19px;top:84px;font-size:20px">Chairs<br><span class="mark">Filled Fast</span></h2>
  <p class="subhead" style="left:19px;top:140px;font-size:16px;width:200px">Attract more clients with simple, strategic digital marketing.</p>
  <div class="copy" style="left:19px;top:211px;width:278px;font-size:7.6px;line-height:1.48">Chairs Filled Fast educates on the ins and outs of sponsored social media ads. With easy-to-follow video training, you’ll establish your online presence and increase salon bookings.<br>Learn how to show up on social media with effective strategies that work. Choose our Handled Entirely system, or learn to do it all with our DIY system.</div>
  <div class="contact" style="left:19px;right:19px;top:289px;font-size:7.4px"><span><svg><use href="#i-phone"/></svg>(+614) 5550 2187</span><span><svg><use href="#i-mail"/></svg>hello@bloombeautyhub.com</span><span><svg><use href="#i-globe"/></svg>www.bloombeautyhub.com</span></div>
</section>

<!-- Skillset Studio Plan, compact -->
<section class="card skillset" style="left:604px;top:691px;width:236px;height:316px">
  <div class="panel"></div>
  <div class="brand" style="left:17px;top:19px"><i></i>Bloom Beauty Hub</div>
  <div class="handle" style="right:18px;top:31px">@bloombeautyhub</div>
  <h2 class="headline" style="left:16px;top:42px;font-size:15.5px">Skillset Studio Plan</h2>
  <p class="subhead" style="left:16px;top:61px;font-size:16px;width:205px">Successfully Upskill and Level Up Your Salon.</p>
  <div class="art" role="img" aria-label="Illustration of a woman sitting on rising pillars with a ladder and a plant" style="left:70px;top:103px;width:96px;height:90px;border-radius:6px;background:linear-gradient(180deg,#4d6684,#f3d9bf 55%,#fbe6cf)"></div>
  <div class="copy" style="left:16px;top:202px;width:203px;font-size:7px;line-height:1.32;color:var(--white)">Skillset Studio Plan offers three training options- In Salon, Online &amp; Diploma of Beauty Therapy. Whether you have your own salon or want to become qualified, Bloom Beauty Hub’s- Skillset Studio Plan adds industry authority and brings specialist expertise to all level of beauty therapists.<br>Our coaching is based in Australia, aim at female beauty salon owners who are ready to take their business to the next level.</div>
  <div class="contact" style="left:18px;right:18px;top:293px"><span><svg><use href="#i-phone"/></svg>(+614) 5550 2187</span><span><svg><use href="#i-mail"/></svg>hello@bloombeautyhub.com</span><span><svg><use href="#i-globe"/></svg>www.bloombeautyhub.com</span></div>
</section>

<!-- Skillset Studio Plan, wide -->
<section class="card skillset" style="left:859px;top:691px;width:314px;height:316px">
  <div class="panel"></div>
  <div class="brand" style="left:21px;top:25px;font-size:7px"><i></i>Bloom Beauty Hub</div>
  <div class="handle" style="right:22px;top:32px;font-size:7.5px">@bloombeautyhub</div>
  <h2 class="headline" style="left:20px;top:42px;font-size:21px">Skillset Studio Plan</h2>
  <p class="subhead" style="left:21px;top:72px;font-size:16.5px;width:270px">Successfully Upskill and Level Up Your Salon.</p>
  <div class="art" role="img" aria-label="Illustration of a woman sitting on rising pillars with a ladder and a plant" style="left:115px;top:116px;width:92px;height:86px;border-radius:6px;background:linear-gradient(180deg,#4d6684,#f3d9bf 55%,#fbe6cf)"></div>
  <div class="copy" style="left:22px;top:215px;width:270px;font-size:7.6px;line-height:1.22;color:var(--white)">Skillset Studio Plan offers three training options- In Salon, Online &amp; Diploma of Beauty Therapy. Whether you have your own salon or want to become qualified, Bloom Beauty Hub’s- Skillset Studio Plan adds industry authority and brings specialist expertise to all level of beauty therapists.<br>Our coaching is based in Australia, aim at female beauty salon owners who are ready to take their business to the next level.</div>
  <div class="contact" style="left:21px;right:22px;top:292px;font-size:7.4px"><span><svg><use href="#i-phone"/></svg>(+614) 5550 2187</span><span><svg><use href="#i-mail"/></svg>hello@bloombeautyhub.com</span><span><svg><use href="#i-globe"/></svg>www.bloombeautyhub.com</span></div>
</section>

</body>
</html>
```